Business Card Design for Vintage Jazz

I am a vintage jazz band leader in New York City. My groups play the music of the 1920s, 1930s and 1940s. My website is morvalquist.com for more info on what I do.

I am looking for a two sided business card design that has the look and feel of a really nice business card from the 1930s. I need to convey with the design that my work has that vintage kind of class and style, but also conveys that we are fun and entertaining.

Most importantly it should make a bold staement. If Hal Denbrook had a card, what would it have looked like? I want a card that I feel confident will make an impact and will let people know that my work is te the top that NYC has to offer in vintage jazz..

Note that I have only decided to avoid the "committed payment" option as I have not used this service before. Assuming that I get quality work I will select a design from those presented.

Target Market(s)

people who want to hire my band for events, media, and new fans of the band

Industry/Entity Type

Performing Art

Contact Information for Business Card

Definitely a matte finish, possibly a sort of old style of paper with that brown tint? definitely a thick card.

Requirements
Must have
• FRONT
• My name: Tobin Vashley
• What I do: Bandleader, Guitarist, Vocalist, Songwriter
• Contact Details: morvalquist.com tobin@morvalquist.com 646-555-0148
• BACK
• My Social Media Links:
• facebook.morvalquist.com
• twitter, instagram, linkedin: morvalquist
• I'm also including a photo image I would like to use. The photo's background is not needed, and to be honest isn't really desireable. Just looking to use the image of me.
Nice to have
• I'm attaching which could be used as is, omitted from the card, or altered maybe with text going around the outside of the circle or in some other way. It may need some clean up to the edges of the lettering as we only use it for the website thumbnail.
• If there's space I'd like to include the text "join our mailing list for a free song download: freesong.morvalquist.com" If not perhaps just "Download a Free Song at: freesong.morvalquist.com - something to this end.
Should not have
• anything cartoony. Don't think retro 90s's vision of the swing era, think actual swing era!
• anything modern. Got to look old school
• Try to avoid dark backgrounds. Since we often play in bars and clubs where it is dar, a d
• avoid script fonts.

```html
<!DOCTYPE html>
<html lang="en">
<head>
<meta charset="utf-8">
<title>Tobin Vashley – Business Card</title>
<link href="https://fonts.googleapis.com/css2?family=Josefin+Sans:wght@400;600&display=swap" rel="stylesheet">
<style>
  :root {
    --backdrop: #e9e4da;
    --paper: #efe4cc;
    --paper-edge: #e2d3b3;
    --ink: #2a2118;
    --ink-soft: #4a3c2e;
    --band: #2a2118;
    --band-text: #f3e9d2;
    --rule: #a8957a;
    --photo-light: #c9b592;
    --photo-dark: #5a4833;
  }
  * { margin: 0; padding: 0; box-sizing: border-box; }
  html, body {
    width: 1200px; height: 900px; overflow: hidden;
    background: var(--backdrop);
    font-family: "Josefin Sans", "Century Gothic", sans-serif;
    color: var(--ink);
  }
  .stage {
    width: 1200px; height: 900px;
    display: flex; align-items: center; justify-content: center; gap: 40px;
  }
  .card {
    position: relative;
    width: 540px; height: 309px;
    border-radius: 18px;
    overflow: hidden;
    background: radial-gradient(ellipse at 50% 40%, var(--paper) 55%, var(--paper-edge) 100%);
    box-shadow: 0 8px 24px rgba(60,45,25,.25);
  }

  /* front */
  .portrait {
    position: absolute; left: 30px; top: 40px;
    width: 220px; height: 192px;
    background: radial-gradient(ellipse at 50% 40%, var(--photo-light) 0%, #8e7758 50%, var(--photo-dark) 100%);
  }
  .front-divider {
    position: absolute; left: 262px; top: 40px;
    width: 1px; height: 192px; background: var(--rule);
  }
  .identity { position: absolute; left: 290px; top: 62px; }
  .identity .name { font-size: 22px; font-weight: 600; letter-spacing: .5px; margin-bottom: 14px; color: var(--ink); }
  .contact-list { list-style: none; }
  .contact-list li {
    display: flex; align-items: center; gap: 9px;
    font-size: 14px; line-height: 21px; color: var(--ink-soft);
  }
  .contact-list svg { width: 11px; height: 11px; flex: none; }
  .role-band {
    position: absolute; left: 0; right: 0; bottom: 0; height: 77px;
    background: var(--band);
    display: flex; align-items: center; justify-content: center;
  }
  .role-band .roles { font-size: 17px; letter-spacing: .4px; color: var(--band-text); padding-left: 60px; }

  /* back */
  .mark {
    position: absolute; left: 0; top: 0; width: 258px; height: 100%;
    display: flex; align-items: center; justify-content: center; gap: 10px;
  }
  .mark .dot { width: 14px; height: 14px; border-radius: 50%; background: var(--ink); flex: none; }
  .mark .wordmark { font-size: 22px; font-weight: 600; letter-spacing: .5px; color: var(--ink); }
  .back-divider {
    position: absolute; left: 258px; top: 22px;
    width: 1px; height: 150px; background: var(--rule);
  }
  .social-list { position: absolute; left: 300px; top: 44px; list-style: none; }
  .social-list li {
    display: flex; align-items: center; gap: 7px;
    font-size: 13px; line-height: 19px; color: var(--ink-soft);
  }
  .social-list .tile { width: 10px; height: 10px; background: var(--ink); border-radius: 1px; flex: none; }
</style>
</head>
<body>
<main class="stage">
  <section class="card card-front">
    <div class="portrait" role="img" aria-label="Sepia photo of the bandleader in a striped blazer tipping a straw boater hat"></div>
    <div class="front-divider"></div>
    <div class="identity">
      <p class="name">Tobin Vashley</p>
      <ul class="contact-list">
        <li>
          <svg viewBox="0 0 12 12" aria-hidden="true"><path fill="#2a2118" d="M2.5 1l2 2.2-1 1.3a7 7 0 0 0 4 4l1.3-1 2.2 2-1.4 1.5C5 11 1 7 1 2.4z"/></svg>
          646-555-0148
        </li>
        <li>
          <svg viewBox="0 0 12 12" aria-hidden="true"><rect x="1" y="2.5" width="10" height="7" fill="#2a2118"/><path d="M1 2.5l5 4 5-4" stroke="#efe4cc" fill="none" stroke-width="1"/></svg>
          tobin@morvalquist.com
        </li>
        <li>
          <svg viewBox="0 0 12 12" aria-hidden="true"><circle cx="6" cy="6" r="5" fill="#2a2118"/><path d="M1 6h10M6 1c-2.5 3-2.5 7 0 10M6 1c2.5 3 2.5 7 0 10" stroke="#efe4cc" fill="none" stroke-width=".8"/></svg>
          morvalquist.com
        </li>
      </ul>
    </div>
    <div class="role-band">
      <p class="roles">Bandleader, Guitarist, Vocalist, Songwriter</p>
    </div>
  </section>

  <section class="card card-back">
    <div class="mark">
      <span class="dot"></span>
      <span class="wordmark">Tobin Vashley</span>
    </div>
    <div class="back-divider"></div>
    <ul class="social-list">
      <li><span class="tile"></span>morvalquist.com</li>
      <li><span class="tile"></span>morvalquist</li>
      <li><span class="tile"></span>morvalquist</li>
      <li><span class="tile"></span>morvalquist</li>
    </ul>
  </section>
</main>
</body>
</html>
```